Tallowood building company Business card design

I need a business card design for my company. I have a logo but dont have business cards with our logo..

www.tallowoodbuildingco.com.au

The logo is on the website

I need the same details as this design I have attached. we have changed the logo and colours. just like the website

Building

```html
<!DOCTYPE html>
<html lang="en">
<head>
<meta charset="utf-8">
<title>Tallowood Building – Business Card</title>
<link rel="stylesheet" href="https://fonts.googleapis.com/css2?family=Cinzel:wght@600&family=Lato:wght@400;700&display=swap">
<style>
  :root {
    --backdrop: #b4b4b4;
    --card: #fbfbfa;
    --brand-blue: #1b88c8;
    --ink: #1a1a1a;
    --on-blue: #ffffff;
  }
  * { margin: 0; padding: 0; box-sizing: border-box; }
  html, body { width: 1200px; height: 800px; overflow: hidden; }
  body {
    background: radial-gradient(ellipse at center, #c9c9c9 0%, var(--backdrop) 70%, #a2a2a2 100%);
    font-family: "Lato", Arial, sans-serif;
    color: var(--ink);
  }
  .business-card {
    position: absolute;
    left: 140px;
    top: 138px;
    width: 920px;
    height: 525px;
    background: var(--card);
    box-shadow: 0 10px 30px rgba(0,0,0,0.18);
    overflow: hidden;
  }
  .brand {
    position: absolute;
    left: 64px;
    top: 64px;
    display: flex;
    align-items: center;
    gap: 16px;
  }
  .brand-square {
    width: 58px;
    height: 58px;
    background: var(--brand-blue);
  }
  .brand-name {
    font-weight: 700;
    color: var(--brand-blue);
    font-size: 30px;
    line-height: 1.1;
    letter-spacing: 1px;
  }
  .contact-list {
    position: absolute;
    left: 64px;
    top: 268px;
    list-style: none;
    font-size: 25px;
    line-height: 38px;
  }
  .contact-list li { display: flex; align-items: center; gap: 16px; }
  .contact-icon { width: 26px; height: 26px; flex: none; }
  .bottom-band {
    position: absolute;
    left: 0;
    bottom: 0;
    width: 920px;
    height: 110px;
  }
  .website {
    position: absolute;
    right: 60px;
    bottom: 22px;
    color: var(--on-blue);
    font-size: 28px;
    letter-spacing: 0.5px;
  }
  .person {
    position: absolute;
    right: 60px;
    top: 300px;
    text-align: right;
  }
  .person-name {
    font-family: "Cinzel", Georgia, serif;
    font-weight: 600;
    font-size: 32px;
    letter-spacing: 1.5px;
  }
  .person-role {
    color: var(--brand-blue);
    font-size: 25px;
    letter-spacing: 1px;
    margin-top: 2px;
  }
</style>
</head>
<body>
  <div class="business-card">
    <div class="brand">
      <div class="brand-square"></div>
      <div class="brand-name">Tallowood<br>Building</div>
    </div>

    <ul class="contact-list">
      <li>
        <svg class="contact-icon" viewBox="0 0 24 24"><path fill="#1b88c8" d="M3 9c0-3 4-5 9-5s9 2 9 5v2h-5V9c-1-1-7-1-8 0v2H3zM6 12h12l2 8H4z"/><circle cx="12" cy="16" r="2" fill="#fff"/></svg>
        <span>9412 5730</span>
      </li>
      <li>
        <svg class="contact-icon" viewBox="0 0 24 24"><rect x="6" y="2" width="12" height="20" rx="2" fill="none" stroke="#1b88c8" stroke-width="2"/><line x1="10" y1="18.5" x2="14" y2="18.5" stroke="#1b88c8" stroke-width="1.5"/></svg>
        <span>0418552904 (Marcus)</span>
      </li>
      <li>
        <svg class="contact-icon" viewBox="0 0 24 24"><rect x="2" y="5" width="20" height="14" fill="#1b88c8"/><path d="M2 5l10 8 10-8M2 19l7-7M22 19l-7-7" fill="none" stroke="#fff" stroke-width="1.5"/></svg>
        <span>info@tallowoodbuildingco.com.au</span>
      </li>
    </ul>

    <svg class="bottom-band" viewBox="0 0 920 110" preserveAspectRatio="none" aria-hidden="true">
      <path d="M0 72 L400 72 C440 72 440 40 480 40 L920 40 L920 110 L0 110 Z" fill="#1b88c8"/>
    </svg>
    <div class="website">www.tallowoodbuildingco.com.au</div>

    <div class="person">
      <div class="person-name">Marcus Ellery</div>
      <div class="person-role">Director</div>
    </div>
  </div>
</body>
</html>
```